TREVAL BUILDWORKS, LLC Webpage portfolio

I want to create a Website that allows my potential clients to browse my Skilled work via before and after photos. I want the website to enhance the work that I provide and potentially drive new business, or at least solidify my work.
I also do 3D CAD and Modeling of New Spaces and it would be nice to show some of that work from pencil design to 3D modeling, which I feel may help give me more clients.

The website needs to show a solid carpenter/company with the skills to get any project completed.

Types of Jobs - Custom Carpentry & Finishes, Kitchens, Baths, Basements, Decks, Porches, Whole House Renovation - Skilled Craftsmanship (Hardwood Flooring, Floor and Wall Tile) and much more...

Target Market(s)

Residential Home Renovation, Kitchen and Bath Renovation, Home Improvement

Industry/Entity Type

Residential Construction

Number of Pages Required

5+ page

Font styles to use
Sans Serif
Script

Requirements
Must have
• Similar to Plinvo.com, except for Treval Buildworks.
• Must be inviting.
• My Services Offered
• A way to reach me or contact me for estimates with some sort of Screening Questionare.
Nice to have
• Inviting Colors
Should not have
• Not sure at this time

```html
<!DOCTYPE html>
<html lang="en">
<head>
<meta charset="utf-8">
<title>Treval Buildworks — My Services</title>
<link rel="stylesheet" href="https://fonts.googleapis.com/css2?family=Questrial&family=Raleway:wght@200;700&display=swap">
<style>
  :root {
    --bg: #232323;
    --stripe: #1a1a1a;
    --text: #ffffff;
    --logo: #d2d2d2;
    --panel-plan: #8a8a8a;
    --panel-room-a: #7d7d7d;
    --panel-room-b: #5e5e5e;
    --panel-warm-a: #7a5444;
    --panel-warm-b: #9a7a63;
  }
  * { margin: 0; padding: 0; box-sizing: border-box; }
  html, body { width: 1200px; height: 260px; overflow: hidden; }
  body {
    position: relative;
    background-color: var(--bg);
    background-image: repeating-linear-gradient(90deg, var(--bg) 0 7px, var(--stripe) 7px 9px);
    color: var(--text);
    font-family: "Questrial", sans-serif;
  }
  .brand {
    position: absolute; left: 50px; top: 44px;
    display: flex; flex-direction: column; align-items: flex-start; gap: 8px;
  }
  .brand-mark { width: 26px; height: 26px; background: var(--logo); margin-left: 8px; }
  .brand-name {
    font-family: "Raleway", sans-serif; font-weight: 700;
    font-size: 14px; color: var(--logo); letter-spacing: 0.2px;
  }
  .social {
    position: absolute; left: 887px; top: 21px;
    display: flex; gap: 13px; list-style: none;
  }
  .social li { width: 13px; height: 13px; border-radius: 50%; background: var(--text); }
  .phone { position: absolute; right: 50px; top: 18px; font-size: 11px; letter-spacing: 0.3px; }
  .main-nav {
    position: absolute; right: 50px; top: 77px;
    display: flex; gap: 20px; list-style: none;
    font-size: 15px; letter-spacing: 0.3px; text-transform: uppercase;
  }
  .services-strip {
    position: absolute; left: 136px; top: 150px; width: 1014px; height: 110px;
    display: flex;
  }
  .services-strip .panel { flex: 1; height: 100%; }
  .panel-design { background: var(--panel-plan); }
  .panel-basement { background: linear-gradient(180deg, var(--panel-room-a), var(--panel-room-b)); }
  .panel-finish { background: linear-gradient(135deg, var(--panel-warm-a), var(--panel-warm-b)); }
  .section-title {
    position: absolute; left: 50px; top: 146px;
    font-family: "Raleway", sans-serif; font-weight: 200;
    font-size: 33px; line-height: 43px; text-transform: uppercase; letter-spacing: 0.5px;
  }
</style>
</head>
<body>
  <header class="site-header">
    <div class="brand">
      <span class="brand-mark"></span>
      <span class="brand-name">Treval Buildworks</span>
    </div>
    <ul class="social" aria-label="Social links">
      <li></li><li></li><li></li><li></li>
    </ul>
    <div class="phone">+8 (555) 210-47-19</div>
    <nav>
      <ul class="main-nav">
        <li>Kitchens</li>
        <li>Baths</li>
        <li>Basements</li>
        <li>Finished Carpentry</li>
        <li>Decks &amp; Porches</li>
      </ul>
    </nav>
  </header>
  <section class="services">
    <div class="services-strip">
      <div class="panel panel-design" role="img" aria-label="Line drawing of a room design plan"></div>
      <div class="panel panel-basement" role="img" aria-label="Basement renovation in progress"></div>
      <div class="panel panel-finish" role="img" aria-label="Finished room with wood trim and ceiling light"></div>
    </div>
    <h1 class="section-title">My<br>Services</h1>
  </section>
</body>
</html>
```